Business Landing Page for SEO Company

Need the landing page of the website designed - I will provide the copy, will need to include details of my company and the services offered, about us, testimonials, faq, etc., and all these elements will need to be arranged graphically on the page.

I want something similar to this: https://torvanequill.com/

Not in terms of color or theme or anything, but we offer a similar service and want to display similar information.

Th services we provide are:

Premium Links
Monthly Links Subscription
Link Insertions

Need to advertise them on the front page. Additionally need a place for testimonials, company details, etc.,

We already have logo for the website. Please use the attached file to insert the logo within the overal design.

Target Market(s)

SEO marketers and agencies

Number of Pages Required

1 page

```html
<!DOCTYPE html>
<html lang="en">
<head>
<meta charset="utf-8">
<title>Lumora – Link Building for SEO Teams</title>
<link href="https://fonts.googleapis.com/css2?family=Montserrat:wght@400;500;600;700&display=swap" rel="stylesheet">
<style>
:root{
  --blue:#2a6fdb;
  --blue-deep:#1553c9;
  --blue-light:#e7f0fb;
  --orange:#ff7f0a;
  --ink:#1e2233;
  --text:#6b6f80;
  --grey-bg:#eef1f7;
  --line:#cfdcf2;
  --footer:#05070d;
  --white:#fff;
}
*{box-sizing:border-box;margin:0;padding:0}
html,body{width:1200px;height:4819px;overflow:hidden}
body{position:relative;font-family:'Montserrat',sans-serif;color:var(--ink);background:var(--white)}
.abs{position:absolute}
.center{text-align:center}

/* header */
.site-header{position:absolute;top:0;left:0;width:1200px;height:84px;background:var(--white)}
.brand{position:absolute;font-weight:700;color:var(--blue);letter-spacing:-1px}
.site-header .brand{left:124px;top:14px;font-size:46px;line-height:1}
.main-nav a{position:absolute;top:36px;font-size:13px;font-weight:500;color:#8a8fa0;text-decoration:none;letter-spacing:.3px}
.main-nav a.active{color:var(--orange)}

/* hero */
.hero{position:absolute;top:84px;left:0;width:1200px;height:700px;background:linear-gradient(180deg,#f2f7fd,#dfeafa)}
.hero-welcome{left:122px;top:170px;font-size:46px;font-weight:400;color:var(--ink)}
.hero-title{left:120px;top:225px;font-size:72px;font-weight:700;color:var(--blue);letter-spacing:-1px}
.hero-tag{left:124px;top:310px;font-size:29px;font-weight:500;color:var(--orange)}
.btn-pill{position:absolute;display:flex;align-items:center;justify-content:center;border-radius:30px;background:var(--orange);color:var(--white);font-weight:700;letter-spacing:1.5px}
.hero .btn-pill{left:124px;top:376px;width:185px;height:42px;font-size:13px}
.hero-art{left:562px;top:47px;width:598px;height:515px;border-radius:50%;background:radial-gradient(circle,#c8dcf7 0%,#d9e7fa 55%,rgba(223,234,250,0) 72%)}
.hero-wave{top:660px;left:0}

/* about */
.about-art{left:150px;top:833px;width:468px;height:459px;border-radius:24px;background:linear-gradient(135deg,#fde3c7,#dbe8fb 60%,#c9dcf7)}
.eyebrow{left:680px;top:911px;font-size:12px;font-weight:600;color:var(--blue);letter-spacing:1.5px}
.about-title{left:679px;top:931px;font-size:33px;font-weight:700;color:var(--ink)}
.about-rule{left:681px;top:976px;width:68px;height:3px;background:var(--orange)}
.about-copy{left:680px;top:1010px;width:420px;font-size:13.5px;line-height:27.5px;color:var(--text)}
.btn-outline{position:absolute;display:flex;align-items:center;justify-content:center;border:2px solid var(--orange);color:var(--orange);font-weight:700;letter-spacing:1.5px}
.about .btn-outline{left:681px;top:1177px;width:166px;height:41px;font-size:13px}

/* services */
.services{position:absolute;top:1357px;left:0;width:1200px;height:661px;background:linear-gradient(180deg,#2b70dc,#1d5fd2);overflow:hidden}
.services-wave{left:0;top:380px;width:1200px;height:281px;background:radial-gradient(ellipse at 50% 90%,rgba(120,170,240,.55),rgba(43,112,220,0) 70%)}
.section-title{position:absolute;left:0;width:1200px;text-align:center;font-size:31px;font-weight:600}
.services .section-title{top:48px;color:var(--white)}
.service{position:absolute;top:122px;width:442px;height:444px}
.service svg.diamond{position:absolute;left:0;top:0}
.service-icon{position:absolute;left:165px;top:80px;width:112px;height:112px;border-radius:50%;display:flex;align-items:center;justify-content:center}
.service h3{position:absolute;left:60px;width:322px;text-align:center;font-size:17px;font-weight:700;line-height:24px}
.service p{position:absolute;left:100px;width:242px;text-align:center;font-size:12px;line-height:19px}
.service .btn-outline{position:absolute;width:122px;height:28px;font-size:10px;border-width:2px}
.service.orange h3,.service.orange p{color:var(--white)}
.service.orange .btn-outline{border-color:var(--white);color:var(--white)}
.service.orange .service-icon{background:var(--white);border:3px solid #ffd7b0}
.service.white h3{color:var(--ink)}
.service.white p{color:var(--text)}
.service.white .service-icon{background:var(--blue);border:4px solid #cfe0fa}

/* testimonials */
.testimonials .section-title{top:2073px;color:var(--ink)}
.title-rule{position:absolute;left:570px;width:60px;height:3px;background:var(--orange)}
.quote-card{position:absolute;top:2215px;width:306px;height:230px;border:2px solid var(--line);background:var(--white);text-align:center}
.quote-card.featured{background:var(--blue);border-color:var(--blue)}
.avatar{position:absolute;left:116px;top:-37px;width:74px;height:74px;border-radius:50%;border:3px solid var(--white);background:linear-gradient(160deg,#c9b8a8,#6d5a4d)}
.quote-card p{position:absolute;left:28px;top:56px;width:250px;font-size:13px;line-height:20.5px;color:var(--text)}
.quote-card .name{position:absolute;left:0;top:172px;width:100%;font-size:12.5px;font-weight:600;color:var(--ink)}
.quote-card.featured p,.quote-card.featured .name{color:var(--white)}
.dots span{position:absolute;top:2483px;width:12px;height:12px;border-radius:50%;background:#9ec0ee}
.dots span.on{background:var(--orange)}

/* blogs */
.blogs{position:absolute;top:2552px;left:0;width:1200px;height:680px;background:var(--grey-bg)}
.blogs .section-title{top:43px;color:var(--ink)}
.blog-card{position:absolute;top:148px;width:308px;height:380px;background:var(--white);border:1px solid #dfe4ee;text-align:center}
.blog-img{width:100%;height:209px}
.blog-card h4{margin:32px 24px 0;font-size:13.5px;font-weight:700;line-height:16px;color:var(--ink)}
.blog-card p{margin:12px 40px 0;font-size:9.5px;line-height:13px;color:var(--text)}
.blog-card .btn-outline{left:94px;top:325px;width:114px;height:31px;font-size:9px;border-radius:20px}

/* faq */
.faq .section-title{top:3241px;color:var(--ink);font-size:27px}
.faq-item{position:absolute;left:207px;width:772px;border:2px solid #c8d2e4;background:var(--white);padding:0 34px}
.faq-item h5{font-size:11.5px;font-weight:600;color:#5d6275;line-height:44px}
.faq-item .chev{position:absolute;right:16px;top:11px}
.faq-item.open{background:var(--orange);border-color:var(--orange);height:148px}
.faq-item.open h5{color:var(--white);line-height:18px;padding-top:28px}
.faq-item.open p{margin-top:16px;font-size:11.5px;line-height:21px;color:#fff2e3}

/* contact */
.contact-bg{left:0;top:3772px}
.contact .section-title{top:3936px;color:var(--white);font-size:31px}
.field{position:absolute;height:48px;border-radius:26px;background:var(--white);padding-left:26px;display:flex;align-items:center;font-size:14px;color:#4a4f60}
.field b{color:var(--orange);font-weight:400}
.field.message{border-radius:14px;align-items:flex-start;padding-top:26px;height:126px}
.contact .btn-pill{left:481px;top:4313px;width:228px;height:49px;font-size:15.5px;letter-spacing:.8px;font-weight:600}

/* footer */
.footer-bg{left:0;top:4380px}
.site-footer .brand{left:0;width:1200px;text-align:center;top:4443px;font-size:50px}
.col-title{position:absolute;top:4553px;font-size:15px;font-weight:600;color:var(--white)}
.footer-links a{position:absolute;font-size:12px;color:#b7bccb;text-decoration:none}
.contact-line{position:absolute;left:548px;display:flex;gap:12px;align-items:flex-start}
.contact-line .lbl{font-size:10px;font-weight:700;color:var(--white);letter-spacing:.5px}
.contact-line .val{font-size:12px;color:#b7bccb;margin-top:2px}
.contact-line.small .val{font-size:10.5px}
.newsletter{left:848px;top:4590px;width:232px;height:36px;border-radius:18px;background:#1d202b;display:flex;align-items:center;padding-left:20px;font-size:12px;color:#9aa0b2}
.newsletter .go{position:absolute;right:6px;top:6px;width:24px;height:24px;border-radius:50%;background:var(--blue);display:flex;align-items:center;justify-content:center}
.social{top:4656px;left:882px;display:flex;gap:9px}
.social span{width:30px;height:30px;border-radius:50%;background:var(--white)}
.social span.first{background:var(--orange)}
.copyright{right:127px;top:4712px;text-align:right;font-size:11.5px;line-height:24px;color:#8a8fa0}
</style>
</head>
<body>

<header class="site-header">
  <div class="brand">lumora</div>
  <nav class="main-nav">
    <a class="active" style="left:407px">HOME</a>
    <a style="left:505px">ABOUT US</a>
    <a style="left:631px">SERVICES</a>
    <a style="left:755px">TESTIMONIALS</a>
    <a style="left:913px">FAQ</a>
    <a style="left:996px">CONTACT</a>
  </nav>
</header>

<section class="hero">
  <div class="abs hero-art" role="img" aria-label="Isometric laptop surrounded by linked web page windows"></div>
  <h2 class="abs hero-welcome">Welcome to</h2>
  <h1 class="abs hero-title">lumora links</h1>
  <p class="abs hero-tag">The Real done for you link</p>
  <a class="btn-pill">LEARN MORE</a>
</section>
<svg class="abs hero-wave" width="1200" height="130" viewBox="0 0 1200 130">
  <path d="M0 14 L600 102 L1200 10 L1200 36 L600 120 L0 42Z" fill="#2a6fdb"/>
  <path d="M0 42 L600 120 L1200 36 L1200 130 L0 130Z" fill="#fff"/>
</svg>

<section class="about">
  <div class="abs about-art" role="img" aria-label="Isometric document board linked to orange and blue web windows"></div>
  <p class="abs eyebrow">WHY WE ARE</p>
  <h2 class="abs about-title">ABOUT LUMORA</h2>
  <div class="abs about-rule"></div>
  <p class="abs about-copy">Lorem ipsum dolor sit amet, consectetur adipiscing elit, sed do eiusmod tempor incididunt ut labore et dolore magna aliqua. Ut enim ad minim veniam, quis nostrud exercitation ullamco laboris nisi Lorem ipsum dolor sit amet, consectetur adipiscing elit, sed do eiusmod</p>
  <a class="btn-outline">LEARN MORE</a>
</section>

<section class="services">
  <div class="abs services-wave" role="img" aria-label="Soft glowing dotted wave texture"></div>
  <h2 class="section-title">OUR SERVICES</h2>

  <div class="service orange" style="left:50px">
    <svg class="diamond" width="442" height="444"><polygon points="221,0 442,222 221,444 0,222" fill="#ff7f0a"/></svg>
    <div class="service-icon">
      <svg width="46" height="46" viewBox="0 0 46 46" fill="none" stroke="#2a6fdb" stroke-width="2.2"><rect x="3" y="7" width="36" height="28" rx="3"/><line x1="3" y1="14" x2="39" y2="14"/><path d="M24 22 L24 40 L29 35 L34 42 L37 40 L32 33 L38 32Z" fill="#fff"/></svg>
    </div>
    <h3 style="top:214px">Premium Links</h3>
    <p style="top:250px">Lorem ipsum dolor sit amet, consectetur adipiscing elit, se</p>
    <a class="btn-outline" style="left:160px;top:300px">LEARN MORE</a>
  </div>

  <div class="service white" style="left:378px">
    <svg class="diamond" width="442" height="444"><polygon points="221,4 438,222 221,440 4,222" fill="#fff" stroke="#2a6fdb" stroke-width="3"/><polygon points="221,14 428,222 221,430 14,222" fill="none" stroke="#cfe0fa" stroke-width="2"/></svg>
    <div class="service-icon">
      <svg width="48" height="48" viewBox="0 0 48 48" fill="none" stroke="#fff" stroke-width="2.2"><rect x="5" y="8" width="34" height="32" rx="3"/><line x1="5" y1="16" x2="39" y2="16"/><line x1="13" y1="4" x2="13" y2="11"/><line x1="31" y1="4" x2="31" y2="11"/><circle cx="36" cy="36" r="8" fill="#2a6fdb"/><path d="M32 36 L35 39 L40 33"/></svg>
    </div>
    <h3 style="top:206px">Monthly Links<br>Subscription</h3>
    <p style="top:258px">Lorem ipsum dolor sit amet, consectetur adipiscing elit sed</p>
    <a class="btn-outline" style="left:161px;top:306px">LEARN MORE</a>
  </div>

  <div class="service orange" style="left:711px">
    <svg class="diamond" width="442" height="444"><polygon points="221,0 442,222 221,444 0,222" fill="#ff7f0a"/></svg>
    <div class="service-icon">
      <svg width="46" height="46" viewBox="0 0 46 46" fill="none" stroke="#2a6fdb" stroke-width="3" stroke-linecap="round"><path d="M20 27 L27 20"/><path d="M18 22 L12 28 a6 6 0 0 0 8 8 L26 30"/><path d="M28 24 L34 18 a6 6 0 0 0 -8 -8 L20 16"/></svg>
    </div>
    <h3 style="top:218px">Link Insertions</h3>
    <p style="top:250px">Lorem ipsum dolor sit amet, consectetur adipiscing elit,</p>
    <a class="btn-outline" style="left:157px;top:296px">LEARN MORE</a>
  </div>
</section>

<section class="testimonials">
  <h2 class="section-title">TESTIMONIALS</h2>
  <div class="title-rule" style="top:2121px"></div>
  <div class="quote-card" style="left:122px">
    <div class="avatar" role="img" aria-label="Client portrait"></div>
    <p>Lorem ipsum dolor sit amet, consectetur adipiscing elit, sed do eiusmod tempor incididunt ut labore et dolore magna aliqua. Ut enim ad minim veniam, quis nostrud</p>
    <div class="name">OWEN HARTLEY</div>
  </div>
  <div class="quote-card featured" style="left:447px">
    <div class="avatar" role="img" aria-label="Client portrait"></div>
    <p>Lorem ipsum dolor sit amet, consectetur adipiscing elit, sed do eiusmod tempor incididunt ut labore et dolore magna aliqua. Ut enim ad minim veniam, quis nostrud</p>
    <div class="name">RHEA CALLOWAY</div>
  </div>
  <div class="quote-card" style="left:769px">
    <div class="avatar" role="img" aria-label="Client portrait"></div>
    <p>Lorem ipsum dolor sit amet, consectetur adipiscing elit, sed do eiusmod tempor incididunt ut labore et dolore magna aliqua. Ut enim ad minim veniam, quis nostrud</p>
    <div class="name">TOMAS VERLUND</div>
  </div>
  <div class="dots"><span style="left:571px"></span><span style="left:594px"></span><span class="on" style="left:617px"></span></div>
</section>

<section class="blogs">
  <h2 class="section-title">LATEST BLOGS</h2>
  <div class="title-rule" style="top:92px"></div>
  <article class="blog-card" style="left:124px">
    <div class="blog-img" role="img" aria-label="Illustration of connected web pages around a monitor" style="background:linear-gradient(135deg,#5aa7ea,#2f7fd9)"></div>
    <h4>Lorem ipsum dolor sit amet, consectetur adipiscing elit, sed do</h4>
    <p>Lorem ipsum dolor sit amet, consectetur adipiscing elit, sed do eiusmod tempor</p>
    <a class="btn-outline">LEARN MORE</a>
  </article>
  <article class="blog-card" style="left:449px">
    <div class="blog-img" role="img" aria-label="Photo of hands typing on a laptop on a wooden desk" style="background:linear-gradient(135deg,#8a6a44,#3b3a3c 55%,#6d5237)"></div>
    <h4>Lorem ipsum dolor sit amet, consectetur adipiscing elit, sed do</h4>
    <p>Lorem ipsum dolor sit amet, consectetur adipiscing elit, sed do eiusmod tempor</p>
    <a class="btn-outline">LEARN MORE</a>
  </article>
  <article class="blog-card" style="left:775px">
    <div class="blog-img" role="img" aria-label="Illustration of a handshake above a linked laptop network" style="background:linear-gradient(135deg,#2a8ad8,#1f6fc4)"></div>
    <h4>Lorem ipsum dolor sit amet, consectetur adipiscing elit, sed do</h4>
    <p>Lorem ipsum dolor sit amet, consectetur adipiscing elit, sed do eiusmod tempor</p>
    <a class="btn-outline">LEARN MORE</a>
  </article>
</section>
<svg class="abs" style="left:0;top:3100px" width="1200" height="140" viewBox="0 0 1200 140">
  <path d="M0 0 H1200 V50 L600 118 L0 22Z" fill="#eef1f7"/>
  <path d="M0 22 L600 118 L600 121 L0 26Z" fill="#2a6fdb"/>
  <path d="M600 118 L1200 50 L1200 64 L600 124Z" fill="#2a6fdb"/>
</svg>

<section class="faq">
  <h2 class="section-title">FREQUENTLY ASKED QUESTIONS</h2>
  <div class="title-rule" style="top:3289px"></div>
  <div class="faq-item open" style="top:3344px">
    <h5>Lorem ipsum dolor sit amet, consectetur adipiscing elit ?</h5>
    <p>Sed ut perspiciatis unde omnis iste natus error sit voluptatem accusantium doloremque laudantium, totam rem aperiam, eaque ipsa quae ab illo inventore veritatis et quasi architecto beatae vitae dicta sunt explicabo. Nemo enim ipsam voluptatem quia voluptas sit aspernatur aut odit aut fugit, sed quia consequuntur magni dolores eos</p>
    <svg class="chev" width="24" height="24" viewBox="0 0 24 24" fill="none" stroke="#fff" stroke-width="1.6"><circle cx="12" cy="12" r="10"/><path d="M7 14 L12 9 L17 14"/></svg>
  </div>
  <div class="faq-item" style="top:3510px"><h5>Sed ut perspiciatis unde omnis iste natus ?</h5><svg class="chev" width="24" height="24" viewBox="0 0 24 24" fill="none" stroke="#2a6fdb" stroke-width="1.4"><circle cx="12" cy="12" r="10"/><path d="M7 10 L12 15 L17 10"/></svg></div>
  <div class="faq-item" style="top:3570px"><h5>Error sit voluptatem accusantium doloremque laudantium ?</h5><svg class="chev" width="24" height="24" viewBox="0 0 24 24" fill="none" stroke="#2a6fdb" stroke-width="1.4"><circle cx="12" cy="12" r="10"/><path d="M7 10 L12 15 L17 10"/></svg></div>
  <div class="faq-item" style="top:3630px"><h5>Ttotam rem aperiam, eaque ipsa quae ab illo inventore ?</h5><svg class="chev" width="24" height="24" viewBox="0 0 24 24" fill="none" stroke="#2a6fdb" stroke-width="1.4"><circle cx="12" cy="12" r="10"/><path d="M7 10 L12 15 L17 10"/></svg></div>
  <div class="faq-item" style="top:3690px"><h5>Weritatis et quasi architecto beatae vitae dicta ?</h5><svg class="chev" width="24" height="24" viewBox="0 0 24 24" fill="none" stroke="#2a6fdb" stroke-width="1.4"><circle cx="12" cy="12" r="10"/><path d="M7 10 L12 15 L17 10"/></svg></div>
</section>

<svg class="abs contact-bg" width="1200" height="660" viewBox="0 0 1200 660">
  <defs><linearGradient id="contactGrad" x1="0" y1="0" x2="0" y2="1"><stop offset="0" stop-color="#1e5fd6"/><stop offset="1" stop-color="#1246b8"/></linearGradient></defs>
  <path d="M0 0 L1200 66 V660 H0Z" fill="url(#contactGrad)"/>
</svg>
<section class="contact">
  <h2 class="section-title">FILL OUR CONTACT FORM</h2>
  <div class="title-rule" style="top:3989px;background:#fff"></div>
  <div class="field" style="left:183px;top:4025px;width:407px">First Name<b>*</b></div>
  <div class="field" style="left:601px;top:4025px;width:408px">Last Name<b>*</b></div>
  <div class="field" style="left:183px;top:4094px;width:407px">Contact Number<b>*</b></div>
  <div class="field" style="left:601px;top:4094px;width:408px">E-mail address<b>*</b></div>
  <div class="field message" style="left:189px;top:4163px;width:824px">Leave a Message</div>
  <a class="btn-pill">SEND MESSAGE</a>
</section>

<svg class="abs footer-bg" width="1200" height="439" viewBox="0 0 1200 439">
  <path d="M0 20 L600 60 L1200 0 V439 H0Z" fill="#05070d"/>
</svg>
<footer class="site-footer">
  <div class="brand">lumora</div>
  <h6 class="col-title" style="left:140px">INFORMATION</h6>
  <nav class="footer-links">
    <a style="left:142px;top:4592px">Home</a>
    <a style="left:142px;top:4624px">About Us</a>
    <a style="left:142px;top:4657px">Services</a>
    <a style="left:142px;top:4689px">News &amp; Blogs</a>
    <a style="left:142px;top:4723px">Contact</a>
  </nav>
  <h6 class="col-title" style="left:355px">LINKS</h6>
  <nav class="footer-links">
    <a style="left:357px;top:4592px">Careers</a>
    <a style="left:357px;top:4624px">Support</a>
    <a style="left:357px;top:4657px">Sitemap</a>
    <a style="left:357px;top:4689px">Privacy Policy</a>
    <a style="left:357px;top:4723px">Contact Us</a>
  </nav>
  <h6 class="col-title" style="left:545px">CONTACT US</h6>
  <div class="contact-line small" style="top:4590px">
    <svg width="28" height="30" viewBox="0 0 28 30" fill="none" stroke="#fff" stroke-width="1.5"><path d="M14 22 C8 15 6 12 6 9 a8 8 0 0 1 16 0 c0 3 -2 6 -8 13Z"/><circle cx="14" cy="9" r="3"/><ellipse cx="14" cy="25" rx="11" ry="3"/></svg>
    <div><div class="lbl">ADDRESS</div><div class="val">418 Alder Crest Lane Fairhaven</div></div>
  </div>
  <div class="contact-line" style="top:4650px">
    <svg width="28" height="28" viewBox="0 0 28 28" fill="none" stroke="#fff" stroke-width="1.5"><path d="M5 4 L10 4 L12 10 L9 12 a14 14 0 0 0 7 7 L18 16 L24 18 L24 23 a2 2 0 0 1 -2 2 A20 20 0 0 1 3 6 a2 2 0 0 1 2 -2Z"/></svg>
    <div><div class="lbl">PHONE</div><div class="val">(555)-410-3827</div></div>
  </div>
  <div class="contact-line" style="top:4708px">
    <svg width="28" height="24" viewBox="0 0 28 24" fill="none" stroke="#fff" stroke-width="1.5"><rect x="2" y="3" width="24" height="18"/><path d="M2 3 L14 13 L26 3"/></svg>
    <div><div class="lbl">EMAIL US</div><div class="val">hello@lumora.com</div></div>
  </div>
  <h6 class="col-title" style="left:848px;top:4559px">NEWSLETTER</h6>
  <div class="abs newsletter">Your E-mail
    <span class="go"><svg width="12" height="12" viewBox="0 0 12 12" fill="none" stroke="#fff" stroke-width="1.8"><path d="M2 6 H10 M6 2 L10 6 L6 10"/></svg></span>
  </div>
  <div class="abs social" aria-label="Social profiles"><span class="first"></span><span></span><span></span><span></span><span></span></div>
  <p class="abs copyright">Copyright © 2021 Lumora.<br>All Right Reserved</p>
</footer>

</body>
</html>
```